BOLD & MINIMALIST DESIGN NEEDED

We want a very bold but minimalistic business card design that is impactful and utilizes both sides of the business card. Our current logo is included for your use.

We want bold fonts and good use of negative space. We don't want the logo to overpower the design.

Target Market(s)

Professionals who are building new commercial buildings.

Industry/Entity Type

Construction

Contact Information for Business Card

Name, Title, email, office phone, cell phone, website

Font styles to use
Serif
Sans Serif

Requirements
Must have
• Bold design!

```html
<!DOCTYPE html>
<html lang="en">
<head>
<meta charset="utf-8">
<title>Stonecrest Business Card</title>
<link href="https://fonts.googleapis.com/css2?family=Roboto:wght@400;700&display=swap" rel="stylesheet">
<style>
  :root {
    --canvas: #e4e4e4;
    --card-white: #ffffff;
    --card-dark: #2f2f2f;
    --ink: #111111;
    --ink-soft: #555555;
    --rule: #c9c9c9;
    --green: #7cc22a;
    --green-light: #c4e39a;
    --black-band: #0d0d0d;
  }
  * { margin: 0; padding: 0; box-sizing: border-box; }
  html, body { width: 1200px; height: 1200px; overflow: hidden; }
  body {
    background: var(--canvas);
    font-family: "Roboto", Arial, sans-serif;
    position: relative;
  }
  .card {
    position: absolute;
    width: 689px;
    height: 394px;
    overflow: hidden;
  }
  .card--front { left: 267px; top: 159px; background: var(--card-white); }
  .card--back { left: 262px; top: 653px; background: var(--card-dark); }

  /* front */
  .brand {
    position: absolute;
    right: 46px;
    top: 128px;
    display: flex;
    align-items: center;
    gap: 10px;
  }
  .brand__mark { width: 22px; height: 22px; background: var(--green); }
  .brand__name {
    font-weight: 700;
    font-size: 36px;
    letter-spacing: 1px;
    color: var(--ink);
  }
  .person { position: absolute; left: 48px; top: 218px; }
  .person__name {
    font-weight: 700;
    font-size: 28px;
    letter-spacing: 0.5px;
    color: var(--ink);
    line-height: 1;
  }
  .person__title {
    font-size: 16px;
    color: var(--green);
    margin-top: 6px;
  }
  .divider {
    position: absolute;
    left: 48px;
    top: 280px;
    width: 596px;
    height: 1px;
    background: var(--rule);
  }
  .contacts {
    position: absolute;
    left: 44px;
    top: 290px;
    list-style: none;
  }
  .contacts li {
    display: flex;
    align-items: center;
    gap: 9px;
    font-size: 16px;
    color: var(--ink-soft);
    height: 20px;
  }
  .contacts svg { width: 14px; height: 14px; fill: var(--ink); flex: none; }
  .band-green {
    position: absolute;
    left: 0;
    bottom: 2px;
    width: 440px;
    height: 15px;
    background: linear-gradient(90deg, var(--green) 0%, var(--green-light) 50%, var(--green) 100%);
  }
  .band-black {
    position: absolute;
    right: 0;
    bottom: 0;
    width: 278px;
    height: 33px;
    background: var(--black-band);
    clip-path: polygon(30px 0, 100% 0, 100% 100%, 0 100%);
  }
  .band-black__url {
    position: absolute;
    right: 42px;
    bottom: 7px;
    font-size: 17px;
    color: #ffffff;
  }

  /* back */
  .back-brand {
    position: absolute;
    left: 0; right: 0;
    top: 160px;
    display: flex;
    justify-content: center;
    align-items: center;
    gap: 14px;
  }
  .back-brand__mark { width: 30px; height: 30px; background: var(--green); }
  .back-brand__name {
    font-weight: 700;
    font-size: 50px;
    letter-spacing: 2px;
    color: #ffffff;
  }
  .back-url {
    position: absolute;
    left: 0; right: 0;
    top: 328px;
    text-align: center;
    font-size: 17px;
    letter-spacing: 3.5px;
    color: #ffffff;
  }
  .back-url__domain { color: var(--green); font-weight: 700; }
</style>
</head>
<body>
  <section class="card card--front">
    <div class="brand">
      <span class="brand__mark"></span>
      <span class="brand__name">STONECREST</span>
    </div>

    <div class="person">
      <h1 class="person__name">MARA ELLISON</h1>
      <p class="person__title">President</p>
    </div>

    <div class="divider"></div>

    <ul class="contacts">
      <li>
        <svg viewBox="0 0 24 24" aria-hidden="true"><path d="M6.6 10.8a15.1 15.1 0 0 0 6.6 6.6l2.2-2.2a1 1 0 0 1 1-.25 11.4 11.4 0 0 0 3.6.57 1 1 0 0 1 1 1V20a1 1 0 0 1-1 1A17 17 0 0 1 3 4a1 1 0 0 1 1-1h3.5a1 1 0 0 1 1 1c0 1.25.2 2.45.57 3.57a1 1 0 0 1-.25 1z"/></svg>
        555-014-2287
      </li>
      <li>
        <svg viewBox="0 0 24 24" aria-hidden="true"><path d="M7 1h10a2 2 0 0 1 2 2v18a2 2 0 0 1-2 2H7a2 2 0 0 1-2-2V3a2 2 0 0 1 2-2zm0 3v14h10V4zm5 15.5a1.2 1.2 0 1 0 0 2.4 1.2 1.2 0 0 0 0-2.4z"/></svg>
        555-019-6630
      </li>
      <li>
        <svg viewBox="0 0 24 24" aria-hidden="true"><path d="M2 5h20v14H2zm2 2v.4l8 5.2 8-5.2V7zm0 2.8V17h16V9.8l-8 5.2z"/></svg>
        info@stonecrestbuild.com
      </li>
    </ul>

    <div class="band-green"></div>
    <div class="band-black"></div>
    <span class="band-black__url">www.stonecrestbuild.com</span>
  </section>

  <section class="card card--back">
    <div class="back-brand">
      <span class="back-brand__mark"></span>
      <span class="back-brand__name">STONECREST</span>
    </div>
    <p class="back-url">www.<span class="back-url__domain">stonecrestbuild</span>.com</p>
  </section>
</body>
</html>
```